Executive recruiting firm in need of business card design

Executive recruiting firm looking for a sleek, classy and modern business card design; card itself will be square shape, rounded edges and soft touch paper, our colors are dark blues in the navy color scale, silvers and grays. Reference our website for a better idea of our company's feel and goals at Tarvex-Up.com - our company message is "Lasting Teams Start With the Right Hire" this should be on the card

```html
<!DOCTYPE html>
<html lang="en">
<head>
<meta charset="utf-8">
<title>Tarvex Up – Business Card</title>
<link rel="stylesheet" href="https://fonts.googleapis.com/css2?family=Open+Sans:ital,wght@0,400;1,400;1,700&display=swap">
<style>
  :root {
    --stage: #141416;
    --navy: #17174d;
    --navy-deep: #121240;
    --white: #ffffff;
    --silver: #d9dbe3;
    --gray: #8a8a96;
  }
  * { box-sizing: border-box; margin: 0; padding: 0; }
  html, body { width: 1200px; height: 963px; overflow: hidden; background: var(--stage); }
  .canvas {
    position: relative; width: 1200px; height: 963px;
    display: flex; align-items: center; justify-content: center; gap: 40px;
  }
  .card {
    position: relative; width: 540px; height: 310px;
    border-radius: 18px; overflow: hidden;
  }

  /* Front */
  .card-front { background: var(--white); }
  .front-band {
    position: absolute; left: 0; right: 0; top: 152px; height: 118px;
    background: var(--navy);
  }
  .identity {
    position: absolute; left: 34px; top: 92px;
    font-family: "Open Sans", sans-serif; color: var(--navy);
  }
  .identity .name { font-weight: 700; font-style: italic; font-size: 19px; letter-spacing: -0.3px; }
  .identity .role { font-style: italic; font-size: 12px; color: var(--gray); margin-top: 1px; }
  .contacts {
    position: absolute; left: 34px; top: 166px;
    font-family: "Open Sans", sans-serif; font-style: italic;
    font-size: 11px; line-height: 16px; color: var(--white);
  }
  .contacts li { list-style: none; display: flex; align-items: center; gap: 8px; }
  .contacts svg { width: 11px; height: 11px; flex: none; }
  .contacts .address { margin-top: 6px; }

  .brand {
    position: absolute; text-align: right;
    font-family: "Open Sans", sans-serif; font-weight: 400;
  }
  .brand .wordmark { font-size: 30px; letter-spacing: 1px; line-height: 1; }
  .brand .descriptor { font-size: 11px; letter-spacing: 0.5px; margin-top: 6px; }
  .card-front .brand { right: 34px; top: 64px; color: var(--navy); }

  /* Back */
  .card-back {
    background: radial-gradient(ellipse at 50% 40%, #1e1e5c 0%, var(--navy-deep) 80%);
  }
  .card-back .brand { left: 0; right: 0; top: 108px; text-align: center; color: var(--silver); }
  .tagline {
    position: absolute; left: 0; right: 0; top: 196px; text-align: center;
    font-family: "Open Sans", sans-serif; font-weight: 400;
    font-size: 12px; letter-spacing: 0.4px; color: var(--silver);
  }
</style>
</head>
<body>
<main class="canvas">
  <section class="card card-front" aria-label="Card front">
    <div class="front-band"></div>

    <div class="identity">
      <p class="name">Marlene Ashby</p>
      <p class="role">Founder</p>
    </div>

    <ul class="contacts">
      <li>
        <svg viewBox="0 0 12 12"><path d="M3 1l2 2.5-1.2 1.2c.7 1.4 1.8 2.5 3.2 3.2L8.2 6.7 10.7 8.7 9.6 10.8C5.4 10.5 1.5 6.6 1.2 2.4z" fill="none" stroke="#fff" stroke-width="0.9"/></svg>
        +1.212.555.0148
      </li>
      <li>
        <svg viewBox="0 0 12 12"><rect x="3.2" y="1" width="5.6" height="10" rx="1" fill="none" stroke="#fff" stroke-width="0.9"/><line x1="5.2" y1="9.3" x2="6.8" y2="9.3" stroke="#fff" stroke-width="0.9"/></svg>
        917-555-0193
      </li>
      <li>
        <svg viewBox="0 0 12 12"><rect x="1" y="2.5" width="10" height="7" fill="#fff"/><path d="M1 2.5l5 4 5-4" fill="none" stroke="#17174d" stroke-width="0.9"/></svg>
        mashby@tarvex-up.com
      </li>
      <li class="address">118 Halden Avenue Suite # 1407<br>New York NY 10001</li>
    </ul>

    <div class="brand">
      <p class="wordmark">Tarvex Up</p>
      <p class="descriptor">talent acquisition</p>
    </div>
  </section>

  <section class="card card-back" aria-label="Card back">
    <div class="brand">
      <p class="wordmark">Tarvex Up</p>
      <p class="descriptor">talent acquisition</p>
    </div>
    <p class="tagline">Lasting Teams Start With the Right Hire</p>
  </section>
</main>
</body>
</html>
```